BOLD & MINIMALIST DESIGN NEEDED

We want a very bold but minimalistic business card design that is impactful and utilizes both sides of the business card. Our current logo is included for your use.

We want bold fonts and good use of negative space. We don't want the logo to overpower the design.

Target Market(s)

Professionals who are building new commercial buildings.

Industry/Entity Type

Construction

Contact Information for Business Card

Name, Title, email, office phone, cell phone, website

Font styles to use
Serif
Sans Serif

Requirements
Must have
• Bold design!

```html
<!DOCTYPE html>
<html lang="en">
<head>
<meta charset="utf-8">
<title>Ridgeline Design + Build — Business Card</title>
<link href="https://fonts.googleapis.com/css2?family=Montserrat:wght@400;500;800&display=swap" rel="stylesheet">
<style>
  :root {
    --stage: #2e2e2e;
    --green: #86c440;
    --white: #ffffff;
    --ink: #111214;
    --card-w: 540px;
    --card-h: 309px;
    --radius: 24px;
  }
  * { box-sizing: border-box; margin: 0; padding: 0; }
  html, body {
    width: 1200px; height: 689px; overflow: hidden;
    background: var(--stage);
    font-family: "Montserrat", Arial, sans-serif;
  }
  .canvas {
    position: relative; width: 1200px; height: 689px;
    display: flex; align-items: center; justify-content: center; gap: 40px;
  }
  .card {
    position: relative; width: var(--card-w); height: var(--card-h);
    border-radius: var(--radius); overflow: hidden;
    background: var(--green);
  }
  /* Front side */
  .card--front {
    display: flex; align-items: center; justify-content: center;
  }
  .wordmark {
    text-align: center; font-weight: 800; line-height: 1;
    text-transform: uppercase;
  }
  .wordmark__name { display: block; font-size: 58px; letter-spacing: 1px; }
  .wordmark__tag { display: block; font-size: 20px; letter-spacing: 9px; margin-top: 10px; }
  .wordmark--light { color: var(--white); }
  .wordmark--dark { color: var(--ink); }
  .wordmark--dark .wordmark__name { font-size: 36px; }
  .wordmark--dark .wordmark__tag { font-size: 12.5px; letter-spacing: 5.5px; margin-top: 7px; }

  /* Back side */
  .card__shape { position: absolute; inset: 0; }
  .card--back .wordmark {
    position: absolute; left: 22px; top: 128px; width: 250px;
  }
  .contact {
    position: absolute; right: 20px; top: 40px; width: 160px;
    text-align: right; color: var(--white);
  }
  .contact__name { font-size: 20px; font-weight: 800; letter-spacing: 0.3px; line-height: 1.1; white-space: nowrap; }
  .contact__title { font-size: 10.5px; font-weight: 500; letter-spacing: 1px; margin-top: 4px; }
  .contact__address { font-size: 11px; font-weight: 400; line-height: 1.5; margin-top: 14px; }
  .contact__list { list-style: none; margin-top: 14px; font-size: 11px; line-height: 1.8; }
  .contact__list li { display: flex; justify-content: flex-end; align-items: center; gap: 6px; white-space: nowrap; }
  .icon { width: 10px; height: 10px; fill: var(--white); flex: none; }
</style>
</head>
<body>
<main class="canvas">

  <section class="card card--front" aria-label="Card front">
    <p class="wordmark wordmark--light">
      <span class="wordmark__name">Ridgeline</span>
      <span class="wordmark__tag">Design + Build</span>
    </p>
  </section>

  <section class="card card--back" aria-label="Card back">
    <svg class="card__shape" viewBox="0 0 540 309" preserveAspectRatio="none" aria-hidden="true">
      <path fill="#ffffff" d="M0 0 H300 C345 10 348 70 336 130 C322 200 322 260 352 309 H0 Z"/>
      <path fill="#111214" d="M300 0 C345 10 348 70 336 130 C322 200 322 260 352 309 H346 C318 260 316 200 329 130 C340 70 338 22 300 0 Z"/>
    </svg>

    <p class="wordmark wordmark--dark">
      <span class="wordmark__name">Ridgeline</span>
      <span class="wordmark__tag">Design + Build</span>
    </p>

    <div class="contact">
      <h1 class="contact__name">MARCUS HALE</h1>
      <p class="contact__title">OWNER-CEO</p>
      <p class="contact__address">Your address<br>City State, Zip 1234</p>
      <ul class="contact__list">
        <li>123 456 789
          <svg class="icon" viewBox="0 0 24 24" aria-hidden="true"><path d="M6.6 10.8a15 15 0 0 0 6.6 6.6l2.2-2.2c.3-.3.7-.4 1-.2 1.1.4 2.3.6 3.6.6.6 0 1 .4 1 1V20c0 .6-.4 1-1 1A17 17 0 0 1 3 4c0-.6.4-1 1-1h3.5c.6 0 1 .4 1 1 0 1.3.2 2.5.6 3.6.1.3 0 .7-.2 1z"/></svg>
        </li>
        <li>123 456 789
          <svg class="icon" viewBox="0 0 24 24" aria-hidden="true"><path d="M7 1h10a2 2 0 0 1 2 2v18a2 2 0 0 1-2 2H7a2 2 0 0 1-2-2V3a2 2 0 0 1 2-2zm0 3v15h10V4zm5 16.2a1 1 0 1 0 0 .1z"/></svg>
        </li>
        <li>info@yourmail.com
          <svg class="icon" viewBox="0 0 24 24" aria-hidden="true"><path d="M2 5h20v14H2zm2 2v.4l8 5.2 8-5.2V7zm0 2.8V17h16V9.8l-8 5.2z"/></svg>
        </li>
        <li>www.yourwebsite.com
          <svg class="icon" viewBox="0 0 24 24" aria-hidden="true"><path d="M12 2a10 10 0 1 0 0 20 10 10 0 0 0 0-20zm6.9 6h-3a15 15 0 0 0-1.3-3.9A8 8 0 0 1 18.9 8zM12 4c.8 1.2 1.5 2.5 1.9 4h-3.8c.4-1.5 1.1-2.8 1.9-4zM4.3 14a8 8 0 0 1 0-4h3.4a16 16 0 0 0 0 4zm.8 2h3a15 15 0 0 0 1.3 3.9A8 8 0 0 1 5.1 16zM8 8H5.1a8 8 0 0 1 4.3-3.9C8.8 5.3 8.4 6.6 8 8zm4 12c-.8-1.2-1.5-2.5-1.9-4h3.8c-.4 1.5-1.1 2.8-1.9 4zm2.3-6H9.7a14 14 0 0 1 0-4h4.6a14 14 0 0 1 0 4zm.3 5.9c.6-1.2 1-2.5 1.3-3.9h3a8 8 0 0 1-4.3 3.9zM16.3 14a16 16 0 0 0 0-4h3.4a8 8 0 0 1 0 4z"/></svg>
        </li>
      </ul>
    </div>
  </section>

</main>
</body>
</html>
```